Heritage Hollow Business Cards

Require a business card design. <br/><br/>Needs to include logo (either round or long version) plus these details:<br/>Maya Torvell<br/>Heritage Hollow<br/>maya@kelvadtrading.com.au<br/>02 6481 7395<br/>PO Box Glenwarra NSW 2791<br/>www.heritagehollow.com.au<br/><br/>I need in an editable format so that I can create for multiple staff members. <br/><br/>

Target Market(s)

We are an online store selling renovation products to home owners are builders. Looking for a classic classy design.

Industry/Entity Type

Home And Garden

Contact Information for Business Card

Maya Torvell
Heritage Hollow
maya@kelvadtrading.com.au
02 6481 7395
PO Box Glenwarra NSW 2791
www.heritagehollow.com.au

Colors

Designer to choose colors to be used in the design.

Requirements
Must have
• Must include Logo.

```html
<!DOCTYPE html>
<html lang="en">
<head>
<meta charset="utf-8">
<title>Heritage Hollow Business Cards</title>
<link href="https://fonts.googleapis.com/css2?family=Arimo:wght@400;700&display=swap" rel="stylesheet">
<style>
  :root {
    --stage: #3a3a3a;
    --card-dark: #231f20;
    --card-light: #ffffff;
    --ink: #1a1a1a;
    --ink-soft: #2b2b2b;
    --mark-light: #e6e6e6;
    --divider: #e2e2e2;
  }
  * { margin: 0; padding: 0; box-sizing: border-box; }
  html, body {
    width: 1200px; height: 1015px; overflow: hidden;
    background: var(--stage);
    font-family: "Arimo", Arial, sans-serif;
  }
  .stage {
    width: 1200px; height: 1015px;
    display: flex; flex-direction: column;
    align-items: center; justify-content: center; gap: 60px;
  }
  .card {
    width: 700px; height: 400px;
    box-shadow: 0 8px 24px rgba(0,0,0,0.35);
    position: relative;
  }
  .card--back {
    background: var(--card-dark);
    display: flex; align-items: center; justify-content: center;
  }
  .brand { display: flex; align-items: center; gap: 18px; }
  .brand__circle {
    width: 74px; height: 74px; border-radius: 50%;
    border: 2px solid var(--mark-light);
  }
  .brand__name {
    font-size: 40px; font-weight: 400; color: var(--mark-light);
    letter-spacing: 0.5px;
  }
  .card--front {
    background: var(--card-light);
    display: flex;
  }
  .front__brand {
    width: 340px; display: flex; align-items: center; justify-content: center;
  }
  .front__brand .brand { gap: 12px; }
  .front__brand .brand__circle { width: 56px; height: 56px; border-color: var(--ink); }
  .front__brand .brand__name { font-size: 28px; color: var(--ink); }
  .front__divider {
    width: 1px; margin: 40px 0; background: var(--divider);
  }
  .front__details {
    flex: 1; padding: 118px 0 0 36px; color: var(--ink-soft);
  }
  .person-name {
    font-size: 22px; font-weight: 700; letter-spacing: 1px;
    text-transform: uppercase; color: var(--ink); margin-bottom: 10px;
  }
  .contact-list { list-style: none; }
  .contact-list li {
    display: flex; align-items: center; gap: 6px;
    font-size: 16px; line-height: 22px;
  }
  .contact-list svg { width: 16px; height: 16px; flex: none; }
  .address { margin-top: 10px; font-size: 16px; line-height: 20px; }
</style>
</head>
<body>
  <main class="stage">
    <section class="card card--back" aria-label="Card back">
      <div class="brand">
        <span class="brand__circle"></span>
        <span class="brand__name">Heritage Hollow</span>
      </div>
    </section>

    <section class="card card--front" aria-label="Card front">
      <div class="front__brand">
        <div class="brand">
          <span class="brand__circle"></span>
          <span class="brand__name">Heritage Hollow</span>
        </div>
      </div>
      <div class="front__divider"></div>
      <div class="front__details">
        <p class="person-name">Maya Torvell</p>
        <ul class="contact-list">
          <li>
            <svg viewBox="0 0 16 16" aria-hidden="true">
              <rect x="0.5" y="0.5" width="15" height="15" rx="2" fill="none" stroke="#1a1a1a"/>
              <path d="M4.5 3.5 L6.5 3.5 L7.2 5.8 L6 6.8 C6.6 8.2 7.8 9.4 9.2 10 L10.2 8.8 L12.5 9.5 L12.5 11.5 C8 11.8 4.2 8 4.5 3.5 Z" fill="#1a1a1a"/>
            </svg>
            02 6481 7395
          </li>
          <li>
            <svg viewBox="0 0 16 16" aria-hidden="true">
              <rect x="0.5" y="3" width="15" height="10" fill="#1a1a1a"/>
              <path d="M0.8 3.3 L8 9 L15.2 3.3" fill="none" stroke="#ffffff" stroke-width="1.2"/>
            </svg>
            maya@kelvadtrading.com.au
          </li>
          <li>
            <svg viewBox="0 0 16 16" aria-hidden="true">
              <circle cx="8" cy="8" r="7.3" fill="#1a1a1a"/>
              <g fill="none" stroke="#ffffff" stroke-width="0.9">
                <ellipse cx="8" cy="8" rx="3" ry="7"/>
                <line x1="1" y1="8" x2="15" y2="8"/>
                <line x1="2.5" y1="4.5" x2="13.5" y2="4.5"/>
                <line x1="2.5" y1="11.5" x2="13.5" y2="11.5"/>
              </g>
            </svg>
            www.heritagehollow.com.au
          </li>
        </ul>
        <p class="address">PO Box Glenwarra<br>NSW 2791</p>
      </div>
    </section>
  </main>
</body>
</html>
```